Corvane Holdings , new business card design

investment firm with corporate clients . need double sided business card , vertical and horizontal options ,logo must be clear. prefer pantone colors only and sharp design. website also www.corvane.ae

Khalid Bin Tarrafi
Managing Director
Tel. +971 4 387 2940
Mobile +971 50 518 2403
khalid@corvane.ae
Q-Span Plaza, officw 18-B07, Warqa Gardens, Dubai

Contact Information for Business Card

Khalid Bin Tarrafi
Managing Director

Font styles to use
Serif

Colors

Designer to choose colors to be used in the design.

```html
<!DOCTYPE html>
<html lang="en">
<head>
<meta charset="utf-8">
<title>Corvane Holdings — Business Card</title>
<link rel="stylesheet" href="https://fonts.googleapis.com/css2?family=Merriweather:wght@300;400&display=swap">
<style>
  :root {
    --page: #ffffff;
    --card: #e0e0e0;
    --slate: #7b838c;
    --slate-soft: #8e959c;
    --navy: #1d2a57;
  }
  html, body {
    margin: 0;
    padding: 0;
    width: 1200px;
    height: 395px;
    overflow: hidden;
    background: var(--page);
  }
  .sheet {
    position: relative;
    width: 1200px;
    height: 395px;
    font-family: "Merriweather", Georgia, serif;
    font-weight: 300;
  }
  .card {
    position: absolute;
    top: 29px;
    width: 531px;
    height: 344px;
    background: var(--card);
    overflow: hidden;
  }
  .card--front { left: 22px; }
  .card--back  { left: 646px; }

  /* Front: company name */
  .wordmark {
    position: absolute;
    left: 0;
    right: 0;
    top: 160px;
    margin: 0;
    text-align: center;
    color: var(--navy);
    font-weight: 300;
    font-size: 22px;
    letter-spacing: 5px;
    text-transform: uppercase;
    line-height: 1;
    padding-left: 5px;
  }

  /* Back: contact block */
  .contact {
    position: absolute;
    left: 31px;
    top: 147px;
    color: var(--slate-soft);
  }
  .contact__name {
    margin: 0;
    font-size: 16px;
    font-weight: 400;
    letter-spacing: 4.2px;
    color: var(--slate);
    line-height: 22px;
  }
  .contact__role {
    margin: 0 0 18px;
    font-size: 16px;
    font-weight: 300;
    letter-spacing: 3.4px;
    line-height: 22px;
  }
  .contact__list {
    list-style: none;
    margin: 0;
    padding: 0;
    font-size: 13px;
    letter-spacing: 2.6px;
    line-height: 22.3px;
  }
  .contact__label {
    color: var(--slate);
    font-weight: 400;
    margin-right: 4px;
  }
  .dot {
    display: inline-block;
    width: 4px;
    height: 4px;
    border: 1px solid var(--slate-soft);
    border-radius: 50%;
    margin: 0 5px;
    vertical-align: middle;
  }
  .website {
    position: absolute;
    left: 501px;
    top: 93px;
    margin: 0;
    writing-mode: vertical-rl;
    transform: rotate(180deg);
    white-space: nowrap;
    color: var(--slate);
    font-size: 12.5px;
    letter-spacing: 3.5px;
    line-height: 1;
  }
</style>
</head>
<body>
<main class="sheet">
  <section class="card card--front" aria-label="Card front">
    <p class="wordmark">Corvane Holdings</p>
  </section>

  <section class="card card--back" aria-label="Card back">
    <div class="contact">
      <p class="contact__name">Khalid Bin Tarrafi</p>
      <p class="contact__role">Managing Director</p>
      <ul class="contact__list">
        <li><span class="contact__label">T</span>+971 4 387 2940</li>
        <li><span class="contact__label">M</span>+971 50 518 2403</li>
        <li>Q-Span Plaza<span class="dot"></span>officw 18-B07</li>
        <li>Warqa Gardens<span class="dot"></span>Dubai</li>
        <li>khalid@corvane.ae</li>
      </ul>
    </div>
    <p class="website">www.corvane.ae</p>
  </section>
</main>
</body>
</html>
```